Local Flower Farm Needs Business Card Design

I need business cards designed for a flower farm based in Eudora, Kansas.
Business Info:
We are a local cut flower farm located in Eudora, Kansas, founded by Corinne Haldwick. What started as a passion for agriculture and search for more joy in daily life has blossomed into a small business dedicated to providing the community with beautiful, fresh, and sustainable flowers. We specialize in local, seasonal blooms, ensuring that every petal reflects the care and dedication we pour into our craft. Our mission is to deliver the highest quality flowers directly to our customers through local farmers markets and to florists who share our commitment to sustainability. Join us in celebrating the beauty of nature, one bloom at a time!
Contact Details:
Corinne Haldwick
Owner
Phone 913-555-0147
Facebook: Rosalind Thorpe Gardens
Instagram: @RosalindThorpeGardens
Website: RosalindThorpeGardens.example
Target Market(s)
Wholesale to Florists and Direct to Consumer via Farmers Market
Industry/Entity Type
Florist, Farm
Contact Information for Business Card
Name, Contact Info, Logo
Look and feel
Each slider illustrates characteristics of the customer's brand and the style your logo design should communicate.

```html
<!DOCTYPE html>
<html lang="en">
<head>
<meta charset="utf-8">
<title>Rosalind Thorpe Gardens – Business Card</title>
<link href="https://fonts.googleapis.com/css2?family=Montserrat:wght@400;500;700&display=swap" rel="stylesheet">
<style>
  :root {
    --backdrop: #3b3b3d;
    --paper: #ffffff;
    --ink: #0c2a30;
    --ink-soft: #1d1d1d;
    --on-dark: #ffffff;
  }
  * { box-sizing: border-box; margin: 0; padding: 0; }
  html, body { width: 1200px; height: 1059px; overflow: hidden; }
  body {
    background: var(--backdrop);
    position: relative;
    font-family: "Montserrat", sans-serif;
  }
  .card {
    position: absolute;
    width: 690px;
    height: 392px;
    border-radius: 18px;
  }
  .card--front { left: 255px; top: 100px; background: var(--paper); }
  .card--back { left: 255px; top: 537px; background: var(--ink); }

  .brand-seal {
    position: absolute;
    border-radius: 50%;
    display: flex;
    align-items: center;
    justify-content: center;
    text-align: center;
    font-family: "Montserrat", sans-serif;
    font-weight: 500;
    text-transform: uppercase;
    letter-spacing: 0.12em;
    line-height: 1.5;
  }
  .card--front .brand-seal {
    left: 42px; top: 76px; width: 236px; height: 236px;
    border: 1px solid var(--ink);
    color: var(--ink);
    font-size: 17px;
  }
  .card--back .brand-seal {
    left: 209px; top: 58px; width: 276px; height: 276px;
    border: 1px solid var(--on-dark);
    color: var(--on-dark);
    font-size: 20px;
  }

  .divider {
    position: absolute;
    left: 306px; top: 76px;
    width: 1.5px; height: 240px;
    background: var(--ink);
  }
  .details {
    position: absolute;
    left: 334px; top: 76px;
    color: var(--ink-soft);
  }
  .details__name {
    font-size: 22px;
    font-weight: 700;
    color: var(--ink);
    letter-spacing: 0.02em;
    text-transform: uppercase;
    line-height: 1.1;
  }
  .details__role {
    font-size: 14px;
    letter-spacing: 0.04em;
    margin-top: 2px;
  }
  .details__rule {
    width: 10px; height: 1.5px;
    background: var(--ink-soft);
    margin: 22px 0 20px;
  }
  .contact-list { list-style: none; }
  .contact-list li {
    display: flex;
    align-items: center;
    gap: 9px;
    font-size: 15px;
    height: 24.5px;
    letter-spacing: 0.01em;
  }
  .contact-list svg { width: 12px; height: 12px; flex: none; }
  .dot { width: 11px; height: 11px; border-radius: 50%; flex: none; background: var(--ink-soft); margin-right: 1px; }
</style>
</head>
<body>
  <section class="card card--front">
    <div class="brand-seal">Rosalind<br>Thorpe<br>Gardens</div>
    <div class="divider"></div>
    <div class="details">
      <h1 class="details__name">Corinne Haldwick</h1>
      <p class="details__role">OWNER</p>
      <div class="details__rule"></div>
      <ul class="contact-list">
        <li>
          <svg viewBox="0 0 24 24" aria-hidden="true"><path fill="#1d1d1d" d="M6.6 10.8a15.1 15.1 0 0 0 6.6 6.6l2.2-2.2c.3-.3.7-.4 1-.2 1.1.4 2.3.6 3.6.6.6 0 1 .4 1 1V20c0 .6-.4 1-1 1A17 17 0 0 1 3 4c0-.6.4-1 1-1h3.5c.6 0 1 .4 1 1 0 1.3.2 2.5.6 3.6.1.3 0 .7-.2 1z"/></svg>
          913-555-0147
        </li>
        <li>
          <svg viewBox="0 0 24 24" aria-hidden="true"><path fill="#1d1d1d" d="M2 5h20v14H2z"/><path fill="none" stroke="#fff" stroke-width="2" d="M2 6l10 7 10-7"/></svg>
          info@RosalindThorpeGardens.example
        </li>
        <li>
          <svg viewBox="0 0 24 24" aria-hidden="true"><g fill="none" stroke="#1d1d1d" stroke-width="2"><circle cx="12" cy="12" r="10"/><ellipse cx="12" cy="12" rx="4" ry="10"/><path d="M2 12h20M4 7h16M4 17h16"/></g></svg>
          www.RosalindThorpeGardens.example
        </li>
      </ul>
      <div class="details__rule"></div>
      <ul class="contact-list">
        <li><span class="dot"></span>Rosalind Thorpe Gardens</li>
        <li><span class="dot"></span>@RosalindThorpeGardens</li>
      </ul>
    </div>
  </section>

  <section class="card card--back">
    <div class="brand-seal">Rosalind<br>Thorpe<br>Gardens</div>
  </section>
</body>
</html>
```